Harborline Lending and Capital. We provide MOSTLY residential home mortgages in Florida AND commercial loans for investment properties throughout the United states.
I would love to emulate so of the lender sites that are available on the internet but I would like to have the site as popular as possible for SEO purposes. Clients can already click the link to take them to the mortgage application where they can complete that and upload documents. If you could polish that up for me that would be great. I can also provide you with great detail on loan programs that are currently being offered. WE OFFER ALL MORTGAGE LENDING PRODUCTS. I would also like to add something in reference to the rate but I don't think it's legal to actually state or promise a rate for mortgage since they vary based on loan type, client and other criteria...

On the Harborline real estate site I would like to add a link or some way for clients to be able to put in credit card information to render services ...

Please let me know what you need from me

Thank you !!

Current link to site to improve and code

https://harborlinelendingandcapital.example/

Industry/Entity Type

Residential and commmercial lending

Coding

Coded - Design and coding required

Number of Pages Required

2 page

Requirements
Must have
• Love to integrate Mortgage interest rates even if general
Nice to have
• Link to fill out mortgage application via Quorvel LPX software

```html
<!DOCTYPE html>
<html lang="en">
<head>
<meta charset="utf-8">
<title>Harborline Lending and Capital — Residential &amp; Commercial Loans</title>
<link href="https://fonts.googleapis.com/css2?family=Poppins:wght@300;400;500;600;700&display=swap" rel="stylesheet">
<style>
:root{
  --forest:#1a2e18;
  --forest-deep:#142412;
  --lime:#7dae31;
  --lime-bright:#8cc43a;
  --ink:#111111;
  --body:#444444;
  --muted:#f0f0f0;
  --white:#ffffff;
  --black:#000000;
}
*{box-sizing:border-box;margin:0;padding:0}
html,body{width:1200px;height:5168px;overflow:hidden}
body{font-family:'Poppins',sans-serif;color:var(--ink);background:var(--white);position:relative}
.abs{position:absolute}
a{color:inherit;text-decoration:none}
.btn{position:absolute;display:flex;align-items:center;justify-content:center;gap:8px;font-size:13px;font-weight:600;letter-spacing:.3px;text-transform:uppercase}
.btn .dot{width:13px;height:13px;border-radius:50%;background:currentColor;position:relative}
.btn .dot::after{content:"";position:absolute;left:4px;top:3.5px;border-left:5px solid var(--dotbg,#000);border-top:3px solid transparent;border-bottom:3px solid transparent}
.btn-dark{background:var(--forest);color:var(--white);--dotbg:var(--forest)}
.btn-lime{background:var(--lime);color:var(--white);--dotbg:var(--lime)}
.rule{position:absolute;height:4px;background:var(--forest)}
.rule-light{background:var(--white)}
.photo{position:absolute}

/* header */
.brand{left:110px;top:14px;display:flex;align-items:center;gap:14px}
.brand-mark{width:72px;height:72px;border-radius:50%;background:var(--forest)}
.brand-name{font-size:11px;font-weight:700;color:var(--forest);text-transform:uppercase;letter-spacing:.2px}
.brand-sub{font-size:8px;letter-spacing:4px;color:#333;text-transform:uppercase;margin-top:6px}
.pay-link{left:646px;top:32px;font-size:13px;text-decoration:underline;color:#222}
.main-nav{left:502px;top:92px;display:flex;gap:22px;font-size:11.5px;font-weight:600;text-transform:uppercase}

/* hero */
.hero{left:0;top:128px;width:1200px;height:542px;background:linear-gradient(180deg,#3a5d92 0%,#7393bf 28%,#9aa69e 50%,#4d6b3a 72%,#2b4a1f 100%)}
.hero-shade{left:0;top:128px;width:1200px;height:542px;background:linear-gradient(90deg,rgba(0,0,0,.45) 0%,rgba(0,0,0,.15) 55%,rgba(0,0,0,.05) 100%)}
.hero-kicker{left:110px;top:466px;font-size:40px;font-weight:400;color:var(--lime);text-transform:uppercase;line-height:1}
.hero-title{left:110px;top:516px;font-size:38px;font-weight:700;color:var(--white);text-transform:uppercase;line-height:1}
.hero-sub{left:114px;top:590px;font-size:16px;font-weight:500;color:var(--white)}
.hero-cta{left:844px;top:580px;width:244px;height:46px;border:2px solid var(--white);color:var(--white);--dotbg:#2a3f22;font-size:12px}

/* about */
.about-title{left:640px;top:796px;font-size:44px;font-weight:700;line-height:1}
.about-title span{color:var(--lime);font-weight:500}
.about-text{left:644px;top:882px;width:450px;font-size:12.5px;line-height:26px;color:var(--body)}

/* sections */
.band-grey{left:0;top:1306px;width:1200px;height:664px;background:var(--muted)}
.sec-title{position:absolute;left:0;width:1200px;text-align:center;font-size:40px;line-height:1.15;text-transform:uppercase}
.sec-title b{font-weight:700}
.sec-title .lime{color:var(--lime);font-weight:500}
.card-label{position:absolute;left:0;bottom:62px;width:100%;text-align:center;font-size:14px;font-weight:600;color:var(--white);text-transform:uppercase}
.arrow{position:absolute;width:26px;height:26px;border-radius:50%}
.arrow svg{display:block}

.band-dark{left:0;top:1970px;width:1200px;height:480px;background:var(--forest)}
.why-title{color:var(--white);font-size:40px;top:2072px}
.why-item{position:absolute;width:340px;text-align:center;color:var(--white)}
.why-item h3{font-size:19px;font-weight:600;text-transform:uppercase;margin-top:18px}
.why-item p{font-size:13px;line-height:23px;margin-top:8px}

.rates-col{position:absolute;width:440px}
.rates-col h3{font-size:17px;font-weight:700;text-transform:uppercase;margin-bottom:14px}
.rates-col p{font-size:12px;line-height:24px;color:var(--body);margin-bottom:8px}
.rates-col p.note{margin-top:22px}

/* estimate */
.estimate{left:0;top:3064px;width:1200px;height:600px;background:linear-gradient(100deg,#3b2a1c 0%,#8a6a4a 30%,#5a4634 55%,#2b2119 100%)}
.estimate-title{left:594px;top:3150px;font-size:40px;line-height:52px;color:var(--white);text-transform:uppercase}
.estimate-title b{font-weight:700}
.calc{left:594px;top:3286px;width:490px;height:294px;background:var(--lime)}
.field{position:absolute;background:var(--white);font-size:11px;color:#555;text-transform:uppercase;display:flex;align-items:center;padding-left:20px}
.upload{flex-direction:column;justify-content:center;padding:0;font-size:8px;text-align:center;line-height:11px}
.apply-btn{left:626px;top:3472px;width:430px;height:76px;background:var(--forest-deep);color:var(--white);text-align:center;flex-direction:column;display:flex;justify-content:center;position:absolute}
.apply-btn small{font-size:10px;text-transform:uppercase}
.apply-btn strong{font-size:16px;font-weight:700;text-transform:uppercase;margin-top:2px}

/* insights */
.post{position:absolute;width:318px}
.post .thumb{width:318px;height:244px}
.post h4{font-size:14.5px;font-weight:600;text-transform:uppercase;line-height:24px;margin-top:14px}
.post p{font-size:12px;line-height:24px;color:var(--body);margin-top:4px}
.post .more{display:flex;align-items:center;gap:8px;font-size:12px;font-weight:600;text-transform:uppercase;margin-top:8px;--dotbg:#fff}
.post .more .dot{width:12px;height:12px;border-radius:50%;background:#000;position:relative}
.post .more .dot::after{content:"";position:absolute;left:4px;top:3px;border-left:5px solid #fff;border-top:3px solid transparent;border-bottom:3px solid transparent}

/* journey */
.journey{left:0;top:4352px;width:1200px;height:522px;background:linear-gradient(90deg,#f6f3ee 0%,#efe9e1 40%,#cdb79a 70%,#8b6a4c 100%)}
.journey-title{left:108px;top:4490px;font-size:42px;line-height:56px;text-transform:uppercase}
.journey-title b{font-weight:700}
.journey-title span{color:var(--lime);font-weight:500}
.journey-text{left:112px;top:4636px;width:360px;font-size:15px;font-weight:600;line-height:30px;text-transform:uppercase}

/* footer */
.footer{left:0;top:4874px;width:1200px;height:294px;background:var(--black)}
.foot-nav{left:0;top:4950px;width:1200px;display:flex;justify-content:center;gap:22px;font-size:11.5px;font-weight:600;color:var(--white);text-transform:uppercase}
.foot-pay{left:548px;top:5010px;font-size:13px;color:var(--white);text-decoration:underline}
.copyright{left:0;top:5096px;width:1200px;text-align:center;font-size:12px;color:var(--white)}
</style>
</head>
<body>

<header>
  <a class="abs brand" href="#">
    <span class="brand-mark" aria-hidden="true"></span>
    <span>
      <span class="brand-name" style="display:block">Harborline Lending and Capital of Florida</span>
      <span class="brand-sub" style="display:block">Business and Commercial Division</span>
    </span>
  </a>
  <a class="abs pay-link" href="#">Pay for Services</a>
  <a class="btn btn-lime" href="#" style="left:788px;top:24px;width:142px;height:38px">Contact Us <span class="dot"></span></a>
  <a class="btn btn-dark" href="#" style="left:946px;top:24px;width:136px;height:38px">Apply Now <span class="dot"></span></a>
  <nav class="abs main-nav">
    <a href="#">Home</a><a href="#">About Us</a><a href="#">Our Loans ⌄</a><a href="#">Loan Programs</a><a href="#">Mortgage Rates</a><a href="#">Resources</a>
  </nav>
</header>

<section>
  <div class="photo hero" role="img" aria-label="Photo of a modern two-storey family home with a green lawn under a blue sky"></div>
  <div class="abs hero-shade"></div>
  <p class="abs hero-kicker">Unlock Your Dream</p>
  <h1 class="abs hero-title">Home or Investment Property!</h1>
  <p class="abs hero-sub">Residential Mortgages in Florida &amp; Commercial Loans Across the U.S.</p>
  <a class="btn hero-cta" href="#">Get Pre-Approved Today <span class="dot"></span></a>
</section>

<section>
  <div class="photo" role="img" aria-label="Aerial photo of a Florida city skyline beside a lake" style="left:110px;top:734px;width:474px;height:472px;background:linear-gradient(180deg,#5f8fd6 0%,#a8c4e6 30%,#6e8a8a 45%,#2c6f96 65%,#3e6b35 100%)"></div>
  <h2 class="abs about-title">About <span>Us</span></h2>
  <div class="rule" style="left:644px;top:850px;width:78px"></div>
  <p class="abs about-text">Harborline Originates Residential Home loans in Florida and Commercial and business financing in all 50 States. We have over 25 years of experience in ALL types of real estate and commercial lending. We are strategically partnered to help you obtain ALL necessary components of residential and commercial lending. From the RIGHT lending partners to the best practice insurance avenues and commercial and residential real estate partners</p>
  <a class="btn btn-dark" href="#" style="left:644px;top:1094px;width:148px;height:40px;font-size:11.5px">View More <span class="dot"></span></a>
</section>

<section>
  <div class="abs band-grey"></div>
  <h2 class="sec-title" style="top:1394px"><b>Find the Loan</b><br><span class="lime">That’s Right for You</span></h2>
  <div class="rule" style="left:562px;top:1514px;width:76px"></div>
  <div class="arrow" style="left:61px;top:1703px;background:var(--lime)"><svg width="26" height="26"><path d="M15 8 L10 13 L15 18" stroke="#fff" stroke-width="2.5" fill="none"/></svg></div>
  <div class="arrow" style="left:1107px;top:1703px;background:#111"><svg width="26" height="26"><path d="M11 8 L16 13 L11 18" stroke="#fff" stroke-width="2.5" fill="none"/></svg></div>
  <div class="photo" role="img" aria-label="Photo of a couple looking at a house" style="left:96px;top:1550px;width:318px;height:338px;background:linear-gradient(180deg,#b9a58d 0%,#6d5846 60%,#3a2c22 100%)"><span class="card-label">Residential Mortgages</span></div>
  <div class="photo" role="img" aria-label="Photo of a smiling business lender at a desk" style="left:440px;top:1550px;width:318px;height:338px;background:linear-gradient(180deg,#6f8aa0 0%,#4d6172 55%,#2f3a44 100%)"><span class="card-label">Commercial Loans</span></div>
  <div class="photo" role="img" aria-label="Illustration of a house with a percent sign over rising bars" style="left:782px;top:1550px;width:318px;height:338px;background:linear-gradient(180deg,#2c4a6e 0%,#1d2f48 60%,#121c2c 100%)"><span class="card-label">Investment Property Loans</span></div>
</section>

<section>
  <div class="abs band-dark"></div>
  <h2 class="sec-title why-title"><b>Why Harborline</b> &nbsp;Mortgage &amp; Finance?</h2>
  <div class="rule rule-light" style="left:572px;top:2142px;width:76px"></div>
  <div class="why-item" style="left:40px;top:2206px">
    <svg width="72" height="66" viewBox="0 0 72 66" fill="none" stroke="#fff" stroke-width="2"><circle cx="40" cy="14" r="5"/><circle cx="54" cy="28" r="5"/><path d="M58 10 L36 32"/><path d="M6 44 L20 40 Q30 38 38 44 L50 44 Q54 46 50 50 L34 50"/><path d="M6 56 L22 54 L58 44 Q64 44 62 50 L30 62 L6 62"/></svg>
    <h3>Competitive Rates</h3>
    <p>Rates tailored to your needs.</p>
  </div>
  <div class="why-item" style="left:422px;top:2206px">
    <svg width="66" height="66" viewBox="0 0 66 66" fill="none" stroke="#fff" stroke-width="2"><circle cx="33" cy="28" r="20"/><circle cx="33" cy="28" r="13"/><path d="M26 29 L31 34 L41 22"/><path d="M22 45 L18 62 L27 57 L33 63 L39 57 L48 62 L44 45"/></svg>
    <h3>Personalized Support</h3>
    <p>Expert guidance at every step</p>
  </div>
  <div class="why-item" style="left:790px;top:2206px">
    <svg width="66" height="66" viewBox="0 0 66 66" fill="none" stroke="#fff" stroke-width="2"><circle cx="33" cy="33" r="26"/><ellipse cx="33" cy="33" rx="11" ry="26"/><path d="M7 33 H59 M11 20 H55 M11 46 H55"/></svg>
    <h3>Nationwide Expertise</h3>
    <p>Residential and commercial loans<br>across the U.S.</p>
  </div>
</section>

<section>
  <h2 class="sec-title" style="top:2546px"><b>Understanding</b> <span class="lime">Mortgage Rates</span></h2>
  <div class="rule" style="left:562px;top:2608px;width:76px"></div>
  <div class="rates-col" style="left:140px;top:2664px">
    <h3 style="margin-left:4px">Fixed-Rate Mortgages:</h3>
    <p>Lorem ipsum dolor sit amet, consectetur adipiscing elit, sed do eiusmod tempor incididunt ut labore et dolore magna aliqua. Ut enim ad minim veniam, quis nostrud exercitation ullamco laboris nisi u</p>
    <p>Lorem ipsum dolor sit amet, consectetur adipiscing elit, sed do eiusmod tempor incididunt ut labore et dolore magna aliqua. Ut enim ad minim veniam, quis nostrud exercitation ullamco laboris nisi u</p>
    <p class="note">Rates vary based on loan type, credit score, and market conditions. Contact us for personalized rates.</p>
  </div>
  <div class="rates-col" style="left:626px;top:2664px">
    <h3 style="color:var(--lime)">Adjustable-Rate Mortgages</h3>
    <p>Lorem ipsum dolor sit amet, consectetur adipiscing elit, sed do eiusmod tempor incididunt ut labore et dolore magna aliqua. Ut enim ad minim veniam, quis nostrud exercitation ullamco laboris nisi u</p>
    <p>Lorem ipsum dolor sit amet, consectetur adipiscing elit, sed do eiusmod tempor incididunt ut labore et dolore magna aliqua. Ut enim ad minim veniam, quis nostrud exercitation ullamco laboris nisi u</p>
    <p class="note">Rates vary based on loan type, credit score, and market conditions. Contact us for personalized rates.</p>
  </div>
</section>

<section>
  <div class="photo estimate" role="img" aria-label="Photo of a small model house with keys on a table, softly blurred"></div>
  <h2 class="abs estimate-title"><b>Estimate Your</b> Monthly<br>Payment</h2>
  <div class="rule rule-light" style="left:596px;top:3264px;width:78px"></div>
  <div class="abs calc"></div>
  <div class="field" style="left:626px;top:3322px;width:288px;height:56px">Loan Amount</div>
  <div class="field" style="left:924px;top:3322px;width:132px;height:56px">Rate of %</div>
  <div class="field" style="left:626px;top:3398px;width:128px;height:56px">Loan Term</div>
  <div class="field" style="left:768px;top:3398px;width:180px;height:56px">Down Payment</div>
  <div class="field upload" style="left:962px;top:3394px;width:94px;height:60px">
    <svg width="14" height="14" viewBox="0 0 14 14"><path d="M7 1 L2 6 H5 V10 H9 V6 H12 Z M2 12 H12 V13.5 H2 Z" fill="#222"/></svg>
    <span>Upload<br>Document</span>
  </div>
  <a class="apply-btn" href="#"><small>Ready to Apply?</small><strong>Start Your Application Now</strong></a>
</section>

<section>
  <h2 class="sec-title" style="top:3758px"><b>Mortgage</b> <span class="lime">Insights &amp; Tips</span></h2>
  <div class="rule" style="left:562px;top:3820px;width:76px"></div>
  <div class="arrow" style="left:61px;top:4019px;background:var(--lime)"><svg width="26" height="26"><path d="M15 8 L10 13 L15 18" stroke="#fff" stroke-width="2.5" fill="none"/></svg></div>
  <div class="arrow" style="left:1111px;top:4019px;background:#111"><svg width="26" height="26"><path d="M11 8 L16 13 L11 18" stroke="#fff" stroke-width="2.5" fill="none"/></svg></div>
  <article class="post" style="left:110px;top:3866px">
    <div class="thumb" role="img" aria-label="Photo of a couple shaking hands with an advisor over a laptop" style="background:linear-gradient(180deg,#d8d2c8 0%,#8c7a68 55%,#3d3228 100%)"></div>
    <h4>Top 5 Tips for First-Time Home Buyers</h4>
    <p>Lorem ipsum dolor sit amet, consectetur adipiscing elit, sed do eiusmod tempor</p>
    <a class="more" href="#">View More <span class="dot"></span></a>
  </article>
  <article class="post" style="left:440px;top:3866px">
    <div class="thumb" role="img" aria-label="Photo of a glass office building at sunset" style="background:linear-gradient(90deg,#c9a98a 0%,#7c8792 50%,#2c3a48 100%)"></div>
    <h4>What to Know ? Commercial Loan Applications</h4>
    <p>Lorem ipsum dolor sit amet, consectetur adipiscing elit, sed do eiusmod tempor</p>
    <a class="more" href="#">View More <span class="dot"></span></a>
  </article>
  <article class="post" style="left:766px;top:3866px">
    <div class="thumb" role="img" aria-label="Photo of city towers against a dramatic evening sky" style="background:linear-gradient(180deg,#3b5f9a 0%,#d0a064 45%,#2e3d52 75%,#1a222c 100%)"></div>
    <h4>How Interest Rates Impact Your Loan</h4>
    <p>Lorem ipsum dolor sit amet, consectetur adipiscing elit, sed do eiusmod tempor</p>
    <a class="more" href="#">View More <span class="dot"></span></a>
  </article>
</section>

<section>
  <div class="photo journey" role="img" aria-label="Photo of a happy family relaxing together at home"></div>
  <h2 class="abs journey-title"><b>Start Your</b> <span>Journey<br>Today</span></h2>
  <div class="rule" style="left:112px;top:4608px;width:78px"></div>
  <p class="abs journey-text">Complete your application in just a few clicks. It’s fast, secure, and hassle-free!</p>
</section>

<footer>
  <div class="abs footer"></div>
  <nav class="abs foot-nav">
    <a href="#">Home</a><a href="#">About Us</a><a href="#">Our Loans ⌄</a><a href="#">Loan Programs</a><a href="#">Mortgage Rates</a><a href="#">Resources</a>
  </nav>
  <a class="btn btn-lime" href="#" style="left:324px;top:5000px;width:144px;height:38px;font-size:12px">Contact Us <span class="dot"></span></a>
  <a class="abs foot-pay" href="#">Pay for Services</a>
  <a class="btn btn-dark" href="#" style="left:728px;top:5000px;width:144px;height:38px;font-size:12px">Apply Now <span class="dot"></span></a>
  <p class="abs copyright">Copyright@2025. All Rights Reserved</p>
</footer>

</body>
</html>
```